Business Card Design Project

Doctor, Pain Management. Need a new business card design with appointment info on the back. New address is 18 Corvell Road, Suite 304, Brisdale, NJ 07391. Right now I believe the rest of the information is staying the same.

```html
<!DOCTYPE html>
<html lang="en">
<head>
<meta charset="utf-8">
<title>Steadfast Pain Care – Business Card</title>
<link rel="stylesheet" href="https://fonts.googleapis.com/css2?family=Roboto+Condensed:wght@400;700&family=Open+Sans:ital,wght@0,400;0,700;1,400&display=swap">
<style>
  :root {
    --backdrop: #e9e6e1;
    --card-black: #151617;
    --card-black-edge: #262829;
    --ink-white: #f2f2f2;
    --ink-grey: #d6d6d6;
    --accent-blue: #6cc7ee;
    --accent-yellow: #e8e24a;
    --rule-grey: #8a8c8e;
    --paper: #ffffff;
    --paper-ink: #1b1b1b;
    --dots: #8d8d8d;
    --faint: #efefef;
  }
  * { box-sizing: border-box; margin: 0; padding: 0; }
  html, body { width: 1200px; height: 950px; overflow: hidden; }
  body {
    background: var(--backdrop);
    position: relative;
    font-family: "Roboto Condensed", "Arial Narrow", sans-serif;
  }
  .card {
    position: absolute;
    left: 250px;
    width: 700px;
    height: 400px;
    border-radius: 4px;
    box-shadow: 0 8px 22px rgba(0,0,0,.22);
    overflow: hidden;
  }

  /* ---------- Front ---------- */
  .card-front {
    top: 55px;
    background: linear-gradient(160deg, var(--card-black-edge) 0%, var(--card-black) 55%, #0e0f10 100%);
    color: var(--ink-white);
  }
  .brand {
    position: absolute;
    left: 260px;
    top: 70px;
    display: flex;
    align-items: center;
    gap: 14px;
  }
  .brand-dot {
    width: 46px; height: 46px;
    border-radius: 50%;
    background: var(--accent-blue);
  }
  .brand-name {
    font-size: 30px;
    font-weight: 400;
    color: var(--accent-yellow);
    letter-spacing: .5px;
  }
  .doctor {
    position: absolute;
    left: 44px;
    top: 182px;
  }
  .doctor-name {
    font-size: 31px;
    font-weight: 400;
    color: var(--accent-blue);
    letter-spacing: .3px;
  }
  .doctor-title {
    font-size: 21px;
    font-weight: 700;
    color: var(--accent-yellow);
    margin-top: 2px;
  }
  .doctor-rule {
    width: 230px;
    height: 1px;
    background: var(--rule-grey);
    margin-top: 12px;
  }
  .contacts {
    position: absolute;
    left: 44px;
    top: 278px;
    list-style: none;
    font-size: 18px;
    line-height: 26px;
    color: var(--ink-grey);
  }
  .contacts li { display: flex; align-items: center; gap: 10px; }
  .contacts svg { width: 15px; height: 15px; flex: none; }
  .divider {
    position: absolute;
    left: 400px;
    top: 262px;
    width: 270px;
    height: 1px;
    background: var(--rule-grey);
  }
  .address {
    position: absolute;
    right: 30px;
    top: 278px;
    font-style: normal;
    text-align: right;
    font-size: 18px;
    line-height: 25px;
    color: var(--ink-grey);
  }

  /* ---------- Back ---------- */
  .card-back {
    top: 495px;
    background: var(--paper);
    color: var(--paper-ink);
    font-family: "Open Sans", Arial, sans-serif;
  }
  .watermark {
    position: absolute;
    left: 250px; top: 90px;
    width: 200px; height: 220px;
    border-radius: 50%;
    background: radial-gradient(ellipse at center, var(--faint) 0%, rgba(239,239,239,0) 72%);
  }
  .appt-title {
    position: absolute;
    top: 44px; left: 0; right: 0;
    text-align: center;
    font-size: 28px;
    font-weight: 700;
  }
  .field-row {
    position: absolute;
    left: 40px; right: 40px; top: 140px;
    display: flex;
    align-items: flex-end;
    gap: 10px;
    font-size: 20px;
  }
  .field-line {
    flex: 1;
    border-bottom: 2px dotted var(--dots);
    height: 22px;
  }
  .field-line.time { flex: .75; }
  .ampm { font-size: 14px; color: #555; }
  .days {
    position: absolute;
    left: 40px; right: 40px; top: 225px;
    display: flex;
    justify-content: space-between;
    list-style: none;
    font-size: 20px;
  }
  .days li { display: flex; align-items: center; gap: 6px; }
  .checkbox {
    width: 18px; height: 18px;
    border: 1.5px solid var(--paper-ink);
  }
  .notice {
    position: absolute;
    left: 40px; right: 40px; top: 305px;
    font-size: 15px;
    font-style: italic;
    line-height: 22px;
  }
</style>
</head>
<body>

<section class="card card-front" aria-label="Business card front">
  <div class="brand">
    <span class="brand-dot"></span>
    <span class="brand-name">Steadfast Pain Care</span>
  </div>

  <div class="doctor">
    <h1 class="doctor-name">LIANWEN ZHAO, M.D., PH.D.</h1>
    <p class="doctor-title">Board Certified Anesthiologist</p>
    <div class="doctor-rule"></div>
  </div>

  <ul class="contacts">
    <li>
      <svg viewBox="0 0 16 16" aria-hidden="true"><path fill="#6cc7ee" d="M4 1l3 3-2 2c1 2 3 4 5 5l2-2 3 3-2 3C7 15 1 9 1 3z"/></svg>
      973.555.0142
    </li>
    <li>
      <svg viewBox="0 0 16 16" aria-hidden="true"><rect x="2" y="5" width="12" height="9" rx="1" fill="#6cc7ee"/><rect x="4" y="1" width="8" height="5" fill="#6cc7ee"/><rect x="4" y="8" width="8" height="1.5" fill="#151617"/></svg>
      973.555.0187
    </li>
    <li>
      <svg viewBox="0 0 16 16" aria-hidden="true"><rect x="1" y="3" width="14" height="10" fill="#6cc7ee"/><path d="M1 3l7 6 7-6" fill="none" stroke="#151617" stroke-width="1.4"/></svg>
      steadfastpain.office@mail.com
    </li>
    <li>
      <svg viewBox="0 0 16 16" aria-hidden="true"><circle cx="8" cy="8" r="7" fill="#6cc7ee"/><path d="M1 8h14M8 1c-3 4-3 10 0 14M8 1c3 4 3 10 0 14" fill="none" stroke="#151617" stroke-width="1"/></svg>
      www.steadfastpc.com
    </li>
  </ul>

  <div class="divider"></div>

  <address class="address">
    18 Corvell Road<br>
    Suite 304<br>
    Brisdale<br>
    NJ 07391
  </address>
</section>

<section class="card card-back" aria-label="Business card back, appointment reminder">
  <div class="watermark" role="img" aria-label="Faint brand decoration"></div>

  <h2 class="appt-title">Next Appointment</h2>

  <div class="field-row">
    <span>Name:</span>
    <span class="field-line"></span>
    <span>Time:</span>
    <span class="field-line time"></span>
    <span class="ampm">AM/PM</span>
  </div>

  <ul class="days">
    <li>Mon <span class="checkbox"></span></li>
    <li>Tue <span class="checkbox"></span></li>
    <li>Wed <span class="checkbox"></span></li>
    <li>Thu <span class="checkbox"></span></li>
    <li>Fri <span class="checkbox"></span></li>
    <li>Sat <span class="checkbox"></span></li>
  </ul>

  <p class="notice">24 hours notice if you are unable to keep your appointment or<br>a cancellation fee may be charged.</p>
</section>

</body>
</html>
```